One Page Website for Personal Trainer in London

I have a logo and need a one page website designed around my branding. I am a freelance Personal Trainer based in London specialising in bodyweight training for men and women. I would like the site to be modern and clean but not overtly urban in design.
I need the following headings:
About Me
My Services
Events
Blog
I don't need them to be seperate pages but if they can link to further down the page that would be great.
Industry/Entity Type
Personal Trainer
Coding
Coded - Design and coding required
Number of Pages Required
1 page
Requirements
Must have
- I need the following headings:
- About Me
- My Services
- Events
- Blog
- mobile friendly formatting
- health and fitness related photography
- Colour scheme in keeping with my existing logo

```html
<!DOCTYPE html>
<html lang="en">
<head>
<meta charset="utf-8">
<title>Maren Holt — Personal Training</title>
<link href="https://fonts.googleapis.com/css2?family=Mulish:wght@400;600;700;800&family=Open+Sans:wght@400;600&display=swap" rel="stylesheet">
<style>
:root{
  --orange:#f7941d;
  --orange-deep:#f26b1d;
  --orange-light:#fbb040;
  --navy:#1f2a5a;
  --dark:#222222;
  --white:#ffffff;
  --grey:#666666;
  --line:#dddddd;
}
*{box-sizing:border-box;margin:0;padding:0}
html,body{width:1200px;height:3502px;overflow:hidden}
body{font-family:"Open Sans",sans-serif;color:var(--dark);background:var(--white);position:relative}
h1,h2,h3,.brand,.nav a{font-family:"Mulish",sans-serif}
section,header,footer{position:absolute;left:0;width:1200px;overflow:hidden}

/* Hero */
.hero{top:0;height:689px}
.hero-photo{position:absolute;inset:0;background:linear-gradient(120deg,#4a4a4a 0%,#8a7a72 35%,#bfb3ab 55%,#6f6560 80%,#3c3a3a 100%)}
.hero-shade{position:absolute;inset:0;background:rgba(0,0,0,.25)}
.brand{position:absolute;left:117px;top:50px;display:flex;align-items:center;gap:12px;color:var(--white);font-weight:700;font-size:30px}
.brand-dot{width:40px;height:40px;border-radius:50%;background:var(--orange)}
.nav{position:absolute;left:500px;top:76px;display:flex;gap:28px}
.nav a{color:var(--white);text-decoration:none;font-size:15px;font-weight:700}
.nav a.active{color:var(--orange)}
.hero-kicker{position:absolute;top:294px;width:100%;text-align:center;color:var(--orange);font-family:"Mulish",sans-serif;font-weight:700;font-size:22px;letter-spacing:5px}
.hero-title{position:absolute;top:322px;width:100%;text-align:center;color:var(--white);font-size:46px;font-weight:800;line-height:52px}
.hero-arrow{position:absolute;top:322px}
.hero-arrow.prev{left:92px}
.hero-arrow.next{right:56px}

/* About */
.about{top:689px;height:549px;background:#f7f3f5}
.about-photo-bg{position:absolute;inset:0;background:linear-gradient(90deg,#f4eef2 0%,#ece0e8 50%,#f6f1f4 100%)}
.about-ring{position:absolute;left:112px;top:51px;width:444px;height:444px;border-radius:50%;background:var(--orange);display:flex;align-items:center;justify-content:center}
.about-ring-inner{width:340px;height:340px;border-radius:50%;background:var(--white);display:flex;align-items:center;justify-content:center}
.about-portrait{width:294px;height:294px;border-radius:50%;background:linear-gradient(180deg,#7fa6c4 0%,#a9b9c4 55%,#d6b59a 100%)}
.about-title{position:absolute;left:598px;top:120px;font-size:34px;font-weight:800;color:var(--navy)}
.about-title span{color:var(--orange)}
.about-text{position:absolute;left:598px;top:172px;width:490px;font-size:15px;line-height:25px;color:var(--grey)}
.about-text p+p{margin-top:8px}

/* Services */
.services{top:1238px;height:551px;background:linear-gradient(110deg,var(--orange-deep) 0%,var(--orange) 55%,var(--orange-light) 100%);color:var(--white)}
.section-title{position:absolute;top:46px;width:100%;text-align:center;font-size:28px;font-weight:800}
.service{position:absolute;width:360px;text-align:center}
.service-icon{width:120px;height:120px;border-radius:50%;border:8px solid var(--white);margin:0 auto 16px;display:flex;align-items:center;justify-content:center}
.service h3{font-size:24px;font-weight:700;margin-bottom:12px}
.service p{font-size:14px;line-height:22px;padding:0 40px}
.service.fitness{left:95px;top:120px}
.service.weight{left:420px;top:126px}
.service.weight .service-icon{position:absolute;left:120px;top:210px;margin:0}
.service.nutrition{left:755px;top:120px}

/* Events */
.events{top:1789px;height:523px;background:var(--dark);color:var(--white)}
.events .section-title{top:50px}
.event{position:absolute;top:119px;width:245px;text-align:center}
.event-photo{width:200px;height:200px;border-radius:50%;border:4px solid var(--white);margin:0 auto 18px}
.event h3{font-size:20px;font-weight:700}
.event .date{font-size:17px;margin:6px 0 12px}
.event p{font-size:13px;line-height:20px;color:#cccccc;padding:0 26px}

/* Blogs */
.blogs{top:2312px;height:553px;background:var(--white)}
.blogs .section-title{color:var(--dark);top:44px}
.post{position:absolute;top:114px;width:304px;height:341px;border:1px solid var(--line);background:var(--white)}
.post-photo{height:185px}
.post-date{position:absolute;left:24px;top:210px;width:50px;height:50px;border-radius:50%;background:var(--orange);color:var(--white);text-align:center;font-family:"Mulish",sans-serif;font-size:20px;font-weight:700;line-height:20px;padding-top:7px}
.post-date small{display:block;font-size:10px;line-height:12px}
.post-body{position:absolute;left:86px;top:208px;right:14px}
.post-body h3{font-size:15px;font-weight:600;margin-bottom:6px}
.post-body p{font-size:11px;line-height:16px;color:var(--grey)}
.post-body .more{display:block;margin-top:10px;font-size:11px;font-weight:700;color:var(--orange);text-decoration:none}
.pager{position:absolute;top:488px;width:100%;display:flex;justify-content:center;gap:10px}
.pager span{width:34px;height:4px;background:#999}
.pager span.on{background:#f0a58a}

/* Contact */
.contact{top:2865px;height:563px;background:linear-gradient(110deg,var(--orange-deep) 0%,var(--orange) 60%,var(--orange-light) 100%);color:var(--white)}
.contact .section-title{top:60px}
.contact-info{position:absolute;top:122px;width:100%;display:flex;justify-content:center;gap:60px;font-size:17px}
.contact-info span{display:flex;align-items:center;gap:8px}
.field{position:absolute;background:var(--white);color:#777;font-size:13px;padding:11px 12px;height:43px}
.field.name{left:156px;top:198px;width:283px}
.field.email{left:453px;top:198px;width:283px}
.field.phone{left:747px;top:198px;width:283px}
.field.message{left:156px;top:248px;width:874px;height:116px}
.submit{position:absolute;left:509px;top:378px;width:182px;height:42px;background:#000;color:var(--white);font-family:"Mulish",sans-serif;font-weight:700;font-size:18px;text-align:center;line-height:42px}
.social{position:absolute;top:442px;width:100%;display:flex;justify-content:center;gap:14px}
.social span{width:48px;height:48px;border-radius:50%;border:2px solid var(--white)}

/* Footer */
.footer{top:3428px;height:74px;background:var(--white);text-align:center;font-size:13px;color:var(--grey);line-height:74px}
</style>
</head>
<body>

<header class="hero">
  <div class="hero-photo" role="img" aria-label="Photo of women training with gym equipment"></div>
  <div class="hero-shade"></div>
  <div class="brand"><span class="brand-dot"></span>Maren Holt</div>
  <nav class="nav">
    <a class="active" href="#top">HOME</a>
    <a href="#about">ABOUT ME</a>
    <a href="#services">MY SERVICES</a>
    <a href="#events">EVENTS</a>
    <a href="#blog">BLOG</a>
    <a href="#contact">CONTACT</a>
  </nav>
  <p class="hero-kicker">PERSONAL TRAINER BASED IN LONDON</p>
  <h1 class="hero-title">BODYWEIGHT TRAINING FOR<br>MEN AND WOMEN</h1>
  <svg class="hero-arrow prev" width="30" height="60" viewBox="0 0 30 60"><polyline points="26,4 4,30 26,56" fill="none" stroke="#fff" stroke-width="3"/></svg>
  <svg class="hero-arrow next" width="30" height="60" viewBox="0 0 30 60"><polyline points="4,4 26,30 4,56" fill="none" stroke="#fff" stroke-width="3"/></svg>
</header>

<section class="about" id="about">
  <div class="about-photo-bg" role="img" aria-label="Faded photo of a woman stretching"></div>
  <div class="about-ring"><div class="about-ring-inner"><div class="about-portrait" role="img" aria-label="Portrait of the trainer by the sea"></div></div></div>
  <h2 class="about-title">ABOUT <span>ME</span></h2>
  <div class="about-text">
    <p>Lorem ipsum dolor sit amet tincidunt sed diam donec quis mi sed magna hendrerit accumsan. Suspendisse risus nibh ultricies eu volutpat non condimentum hendrerit augue. Etiam eleifend metus vitae adipiscing semper mauris ipsum iaculis elit congue gravida elit mi egestas orci curabitur pede.</p>
    <p>Maecenas aliquet velit sed turpis mauris neque metus malesuada nec ultricies sit amet porttitor mattis enim in massa.</p>
  </div>
</section>

<section class="services" id="services">
  <h2 class="section-title">OUR SERVICES</h2>
  <div class="service fitness">
    <div class="service-icon"><svg width="60" height="30" viewBox="0 0 60 30"><rect x="2" y="6" width="8" height="18" fill="#fff"/><rect x="50" y="6" width="8" height="18" fill="#fff"/><rect x="10" y="13" width="40" height="4" fill="#fff"/></svg></div>
    <h3>Fitness Services</h3>
    <p>Maecenas at justo id velit placerat molestie. Donec dictum lectus non odio. Cras a ante vitae enim iaculis aliquam.</p>
  </div>
  <div class="service weight">
    <h3>Weight Loss</h3>
    <p>Maecenas at justo id velit placerat molestie. Donec dictum lectus non odio. Cras a ante vitae enim iaculis aliquam.</p>
    <div class="service-icon"><svg width="50" height="50" viewBox="0 0 50 50"><rect x="4" y="4" width="42" height="42" rx="6" fill="none" stroke="#fff" stroke-width="4"/><circle cx="25" cy="20" r="8" fill="none" stroke="#fff" stroke-width="3"/></svg></div>
  </div>
  <div class="service nutrition">
    <div class="service-icon"><svg width="50" height="50" viewBox="0 0 50 50"><line x1="10" y1="40" x2="40" y2="10" stroke="#fff" stroke-width="8" stroke-linecap="round"/></svg></div>
    <h3>Nutrition Consulting</h3>
    <p>Maecenas at justo id velit placerat molestie. Donec dictum lectus non odio. Cras a ante vitae enim iaculis aliquam.</p>
  </div>
</section>

<section class="events" id="events">
  <h2 class="section-title">OUR EVENTS</h2>
  <article class="event" style="left:120px">
    <div class="event-photo" role="img" aria-label="Photo of runners on a trail" style="background:linear-gradient(160deg,#7d8a5a,#b9a98a)"></div>
    <h3>Event Title here</h3><p class="date">25 Sep 2017</p>
    <p>elit Fusce ultricies orci ac feugiat suscipit leo massa sodales velit et scelerisque mi tortor</p>
  </article>
  <article class="event" style="left:365px">
    <div class="event-photo" role="img" aria-label="Photo of an outdoor group workout" style="background:linear-gradient(160deg,#5f8fb0,#9fb46a)"></div>
    <h3>Event Title here</h3><p class="date">25 Sep 2017</p>
    <p>elit Fusce ultricies orci ac feugiat suscipit leo massa sodales velit et scelerisque mi tortor</p>
  </article>
  <article class="event" style="left:610px">
    <div class="event-photo" role="img" aria-label="Photo of a man doing a jump exercise" style="background:linear-gradient(160deg,#3a3030,#8a6a5a)"></div>
    <h3>Event Title here</h3><p class="date">25 Sep 2017</p>
    <p>elit Fusce ultricies orci ac feugiat suscipit leo massa sodales velit et scelerisque mi tortor</p>
  </article>
  <article class="event" style="left:855px">
    <div class="event-photo" role="img" aria-label="Photo of a boxer in a ring" style="background:linear-gradient(160deg,#c0392b,#c79a7a)"></div>
    <h3>Event Title here</h3><p class="date">25 Sep 2017</p>
    <p>elit Fusce ultricies orci ac feugiat suscipit leo massa sodales velit et scelerisque mi tortor</p>
  </article>
</section>

<section class="blogs" id="blog">
  <h2 class="section-title">OUR BLOGS</h2>
  <article class="post" style="left:126px">
    <div class="post-photo" role="img" aria-label="Photo of a kettlebell workout" style="background:linear-gradient(160deg,#3b2a25,#a06a55)"></div>
    <div class="post-date">01<small>AUG</small></div>
    <div class="post-body"><h3>Blog Title here</h3><p>netus et malesuada fames ac turpis egestas Cras id elit Integer quis urna Ut ante enim dapibus males</p><a class="more" href="#blog">READ MORE</a></div>
  </article>
  <article class="post" style="left:446px">
    <div class="post-photo" role="img" aria-label="Photo of a woman holding a plank" style="background:linear-gradient(160deg,#c9ccd0,#6f7880)"></div>
    <div class="post-date">01<small>AUG</small></div>
    <div class="post-body"><h3>Blog Title here</h3><p>netus et malesuada fames ac turpis egestas Cras id elit Integer quis urna Ut ante enim dapibus males</p><a class="more" href="#blog">READ MORE</a></div>
  </article>
  <article class="post" style="left:766px">
    <div class="post-photo" role="img" aria-label="Photo of fresh food, weights and a scale" style="background:linear-gradient(160deg,#6ec6c9,#e0835a)"></div>
    <div class="post-date">01<small>AUG</small></div>
    <div class="post-body"><h3>Blog Title here</h3><p>netus et malesuada fames ac turpis egestas Cras id elit Integer quis urna Ut ante enim dapibus males</p><a class="more" href="#blog">READ MORE</a></div>
  </article>
  <div class="pager"><span></span><span class="on"></span><span></span></div>
</section>

<section class="contact" id="contact">
  <h2 class="section-title">CONTACT US</h2>
  <div class="contact-info">
    <span><svg width="14" height="20" viewBox="0 0 14 20"><path d="M7 0C3 0 0 3 0 7c0 5 7 13 7 13s7-8 7-13c0-4-3-7-7-7zm0 10a3 3 0 110-6 3 3 0 010 6z" fill="#fff"/></svg>48 Harlow Lane Suite 3 Fairview 20417</span>
    <span><svg width="20" height="20" viewBox="0 0 20 20"><path d="M4 1l4 4-2 3c1 2 4 5 6 6l3-2 4 4-3 3C9 19 1 11 1 4z" fill="none" stroke="#fff" stroke-width="1.6"/></svg>555.014.2290</span>
    <span><svg width="22" height="16" viewBox="0 0 22 16"><rect x="1" y="1" width="20" height="14" fill="none" stroke="#fff" stroke-width="1.6"/><polyline points="1,1 11,9 21,1" fill="none" stroke="#fff" stroke-width="1.6"/></svg>hello@marenholt.com</span>
  </div>
  <div class="field name">NAME</div>
  <div class="field email">EMAIL</div>
  <div class="field phone">PHONE</div>
  <div class="field message">MESSAGE</div>
  <div class="submit">SUBMIT</div>
  <div class="social"><span></span><span></span><span></span><span></span></div>
</section>

<footer class="footer">© 2016 Company Name &nbsp;All right reserved &nbsp;Term of Use</footer>

</body>
</html>
```